Frostvale Harborline LLC

we need a business card design

Industry/Entity Type

hvac

Contact Information for Business Card

my logo

Requirements
Must have
• my logo and same colors

```html
<!DOCTYPE html>
<html lang="en">
<head>
<meta charset="utf-8">
<title>Frostvale Harborline LLC — Business Card</title>
<link rel="stylesheet" href="https://fonts.googleapis.com/css2?family=Montserrat:wght@400;500;700;800&display=swap">
<style>
  :root {
    --brand-blue: #1160aa;
    --brand-navy: #0d4f9c;
    --brand-sky: #1ea0dc;
    --brand-gold: #f3b63a;
    --paper: #ffffff;
    --ink: #2b2b2b;
    --backdrop: #e9ebee;
  }
  * { box-sizing: border-box; margin: 0; padding: 0; }
  html, body {
    width: 1200px; height: 875px; overflow: hidden;
    background: var(--backdrop);
    font-family: "Montserrat", Arial, sans-serif;
  }
  .sheet {
    position: relative; width: 1200px; height: 875px;
    display: flex; align-items: center; justify-content: center; gap: 40px;
  }
  .card {
    width: 540px; height: 309px; border-radius: 16px;
    box-shadow: 0 6px 18px rgba(0,0,0,0.12);
    position: relative; overflow: hidden;
  }
  .card--front {
    background: var(--brand-blue);
    display: flex; align-items: center; justify-content: center;
  }
  .brand-mark {
    display: flex; align-items: center; gap: 14px;
  }
  .brand-mark__dot {
    width: 22px; height: 22px; border-radius: 50%;
    background: var(--brand-gold); flex: none;
  }
  .brand-mark__name {
    font-weight: 800; font-size: 30px; line-height: 1.1;
    color: var(--paper); text-transform: uppercase; letter-spacing: 0.5px;
  }
  .card--back {
    background: var(--paper);
    display: flex; align-items: center;
    padding: 0 34px 0 40px;
  }
  .card--back .brand-mark { width: 210px; gap: 10px; }
  .card--back .brand-mark__dot { width: 16px; height: 16px; }
  .card--back .brand-mark__name { font-size: 21px; color: var(--brand-blue); }
  .divider {
    width: 2px; height: 150px; background: var(--brand-gold);
    margin: 0 26px 0 22px; flex: none;
  }
  .details { color: var(--ink); }
  .details__name {
    font-weight: 800; font-size: 22px; letter-spacing: 0.3px;
    color: var(--brand-navy); text-transform: uppercase;
  }
  .details__name span { color: var(--brand-sky); }
  .details__role { font-size: 13px; margin-bottom: 12px; }
  .details__address { font-size: 12.5px; line-height: 1.4; margin-bottom: 10px; }
  .contact-list { list-style: none; font-size: 12.5px; line-height: 1.6; }
  .contact-list li { display: flex; align-items: center; gap: 7px; }
  .contact-list svg { width: 11px; height: 11px; flex: none; }
</style>
</head>
<body>
<main class="sheet">
  <section class="card card--front" aria-label="Card front">
    <div class="brand-mark">
      <span class="brand-mark__dot"></span>
      <span class="brand-mark__name">Frostvale<br>Harborline LLC</span>
    </div>
  </section>

  <section class="card card--back" aria-label="Card back">
    <div class="brand-mark">
      <span class="brand-mark__dot"></span>
      <span class="brand-mark__name">Frostvale<br>Harborline LLC</span>
    </div>
    <div class="divider"></div>
    <div class="details">
      <p class="details__name">Dorian <span>Welle</span></p>
      <p class="details__role">Founder</p>
      <p class="details__address">4/12 Quarry Ridge Ln<br>Halvercott XYZ 4190</p>
      <ul class="contact-list">
        <li>
          <svg viewBox="0 0 12 12" aria-hidden="true"><path d="M2.5 1h2l1 3-1.3 1a6 6 0 0 0 2.8 2.8l1-1.3 3 1v2a1 1 0 0 1-1 1A9.5 9.5 0 0 1 1.5 2a1 1 0 0 1 1-1z" fill="var(--brand-sky)"/></svg>
          555.214.0386
        </li>
        <li>
          <svg viewBox="0 0 12 12" aria-hidden="true"><rect x="0.5" y="2" width="11" height="8" rx="1" fill="var(--brand-sky)"/><path d="M1 2.6 6 6.5l5-3.9" fill="none" stroke="#fff" stroke-width="1"/></svg>
          hello@frostvaleharbor.com
        </li>
        <li>
          <svg viewBox="0 0 12 12" aria-hidden="true"><circle cx="6" cy="6" r="5" fill="none" stroke="var(--brand-sky)" stroke-width="1.2"/><ellipse cx="6" cy="6" rx="2.2" ry="5" fill="none" stroke="var(--brand-sky)" stroke-width="1"/><path d="M1 6h10" stroke="var(--brand-sky)" stroke-width="1"/></svg>
          www.frostvaleharbor.com
        </li>
      </ul>
    </div>
  </section>
</main>
</body>
</html>
```